Construction Company

Design a clutter free business card, it can be double-sided utilizing the logo for VKM Ltd simple with all relevant contact information.

Please also a letterhead design to function for the purposes of invoicing, all mail requirements, with header to be distinctive while the footer ties page together and incorporates all necessary information.

For now, please use generic / dummy text and when a winner is selected, I will disclose the contact information.

Hi Designers! Please read the updated brief which includes the design of a business card and letterhead. Thank you!

```html
<!DOCTYPE html>
<html lang="en">
<head>
<meta charset="utf-8">
<title>VKM Ltd – Business Card</title>
<link rel="stylesheet" href="https://fonts.googleapis.com/css2?family=Roboto:wght@400;500;700&display=swap">
<style>
  :root {
    --backdrop: #2a2a2a;
    --navy: #002f8e;
    --gold: #b08e05;
    --white: #ffffff;
    --shadow: rgba(0, 0, 0, 0.85);
  }
  * { margin: 0; padding: 0; box-sizing: border-box; }
  html, body {
    width: 1200px;
    height: 801px;
    overflow: hidden;
    background: var(--backdrop);
    font-family: "Roboto", Arial, sans-serif;
  }
  .stage { position: relative; width: 1200px; height: 801px; }

  .card {
    position: absolute;
    top: 274px;
    width: 442px;
    height: 263px;
    box-shadow: 2px 2px 2px var(--shadow);
    overflow: hidden;
  }
  .card--front { left: 154px; background: var(--navy); }
  .card--back { left: 625px; background: var(--white); }

  .card__accent {
    position: absolute;
    top: 0;
    right: 0;
    width: 129px;
    height: 100%;
    background: var(--gold);
  }

  .person { position: absolute; left: 23px; top: 28px; }
  .person__name {
    color: var(--gold);
    font-size: 14.5px;
    font-weight: 500;
    letter-spacing: 0.1px;
    line-height: 16px;
  }
  .person__role {
    color: var(--white);
    font-size: 13px;
    line-height: 15px;
  }

  .contact {
    position: absolute;
    left: 24px;
    top: 128px;
    list-style: none;
    color: var(--white);
    font-size: 13px;
    line-height: 15.6px;
  }
  .contact__item { display: flex; align-items: center; gap: 4px; }
  .contact__icon { width: 12px; height: 12px; flex: none; }

  .address {
    position: absolute;
    left: 24px;
    top: 203px;
    color: var(--white);
    font-size: 13px;
    line-height: 15.6px;
    font-style: normal;
  }

  .brand {
    position: absolute;
    inset: 0;
    display: flex;
    align-items: center;
    justify-content: center;
    gap: 10px;
  }
  .brand__dot {
    width: 18px;
    height: 18px;
    border-radius: 50%;
    background: var(--gold);
  }
  .brand__name {
    color: var(--navy);
    font-size: 44px;
    font-weight: 700;
    letter-spacing: 1px;
  }
</style>
</head>
<body>
<main class="stage">
  <section class="card card--front" aria-label="Business card front">
    <div class="card__accent"></div>

    <div class="person">
      <p class="person__name">MARCUS HALE</p>
      <p class="person__role">Managing Director</p>
    </div>

    <ul class="contact">
      <li class="contact__item">
        <svg class="contact__icon" viewBox="0 0 12 12" aria-hidden="true"><path d="M2.5 1 L4.5 3.3 L3.5 4.6 C4.2 6 5.6 7.5 7.2 8.4 L8.6 7.4 L11 9.4 L9.8 11 C5.5 10.8 1.2 6.5 1 2.3 Z" fill="none" stroke="var(--gold)" stroke-width="1.2" stroke-linejoin="round"/></svg>
        <span>055-917 204 638</span>
      </li>
      <li class="contact__item">
        <svg class="contact__icon" viewBox="0 0 12 12" aria-hidden="true"><rect x="2.5" y="1" width="7" height="10" rx="1" fill="none" stroke="var(--gold)" stroke-width="1.4"/><rect x="5" y="8.8" width="2" height="1" fill="var(--gold)"/></svg>
        <span>055-917 204 639</span>
      </li>
      <li class="contact__item">
        <svg class="contact__icon" viewBox="0 0 12 12" aria-hidden="true"><rect x="0.5" y="3" width="11" height="7" fill="var(--gold)"/><path d="M0.8 3.3 L6 7 L11.2 3.3" fill="none" stroke="var(--navy)" stroke-width="0.9"/></svg>
        <span>hello@vkmltd.com</span>
      </li>
      <li class="contact__item">
        <svg class="contact__icon" viewBox="0 0 12 12" aria-hidden="true"><g fill="none" stroke="var(--gold)" stroke-width="1"><circle cx="6" cy="6.5" r="5"/><ellipse cx="6" cy="6.5" rx="2.2" ry="5"/><path d="M1 6.5 H11 M1.8 4 H10.2 M1.8 9 H10.2"/></g></svg>
        <span>www.vkmbuilders.com</span>
      </li>
    </ul>

    <address class="address">
      18, Harbour Road, Unit 4<br>
      30218, Northland
    </address>
  </section>

  <section class="card card--back" aria-label="Business card back">
    <div class="brand">
      <span class="brand__dot" aria-hidden="true"></span>
      <span class="brand__name">VKM Ltd</span>
    </div>
  </section>
</main>
</body>
</html>
```